Social Media Graphics - Oakline Push REVISED

Create 6-7 individual social media graphics (square size) to encourage folks to join our online course called:

The Harvest Ledger Circle
How to Launch a Multi-Million Business From Scratch
Sign Up Today!

IMPORTANT: Make the largest and most prominent text on the graphic be: How to Launch a Multi-Million Business From Scratch

For the color scheme of the graphics, let's try a blue color palette; make sure the graphics appeal to both men and women

Make sure each graphic contains 1 of the 3 pics attached (crop pic as needed); and make sure one of the graphics is all TEXT only.

Target Market(s)

men and women looking to start a business

Industry/Entity Type

Entrepreneurship

Colors
0054AA
0677BA
7BADD7
CADEEF
E8F1F8

Requirements
Must have
• All the text and use the 3 pics provided; one graphic can be all text; Simple, modern design that's easy to read

```html
<!DOCTYPE html>
<html lang="en">
<head>
<meta charset="utf-8">
<title>The Harvest Ledger Circle – Social Graphic</title>
<link href="https://fonts.googleapis.com/css2?family=Archivo+Black&display=swap" rel="stylesheet">
<style>
  :root {
    --blue-deep: #0054aa;
    --blue-mid: #0677ba;
    --blue-bright: #1a9be8;
    --blue-soft: #7badd7;
    --blue-pale: #cadeef;
    --blue-mist: #e8f1f8;
    --navy: #262c62;
    --navy-dark: #1d2257;
    --cyan: #3ec3e8;
    --white: #ffffff;
    --ink: #2a2a2a;
  }
  html, body {
    margin: 0;
    padding: 0;
    width: 1200px;
    height: 1200px;
    overflow: hidden;
    background: var(--blue-deep);
  }
  .graphic {
    position: relative;
    width: 1200px;
    height: 1200px;
    overflow: hidden;
    font-family: "Archivo Black", "Arial Black", sans-serif;
    color: var(--white);
  }
  .graphic__backdrop {
    position: absolute;
    inset: 0;
  }
  .host-photo {
    position: absolute;
    left: 255px;
    top: 72px;
    width: 753px;
    height: 530px;
    border-radius: 240px 240px 0 0;
    background: linear-gradient(180deg, #23324f 0%, #1a2540 55%, #1e3f6a 100%);
  }
  .course-name {
    position: absolute;
    left: 246px;
    top: 600px;
    width: 709px;
    height: 60px;
    border-radius: 22px 22px 0 0;
    background: linear-gradient(90deg, #231a6e 0%, var(--blue-deep) 55%, #1d1f6a 100%);
    display: flex;
    align-items: center;
    justify-content: center;
    font-size: 34px;
    letter-spacing: 0.5px;
    text-transform: uppercase;
    white-space: nowrap;
  }
  .headline {
    position: absolute;
    left: 120px;
    top: 688px;
    width: 960px;
    margin: 0;
    text-align: center;
    font-size: 81px;
    line-height: 81px;
    font-weight: 400;
    text-transform: uppercase;
    letter-spacing: 1px;
    -webkit-text-stroke: 5px var(--ink);
    paint-order: stroke fill;
  }
  .cta {
    position: absolute;
    left: 360px;
    top: 1067px;
    width: 486px;
    height: 78px;
    border-radius: 39px;
    background: linear-gradient(180deg, #45b9d2 0%, #5cc0ea 45%, #2a9be8 100%);
    display: flex;
    align-items: center;
    justify-content: center;
    font-size: 36px;
    text-transform: uppercase;
    letter-spacing: 0.5px;
    white-space: nowrap;
  }
</style>
</head>
<body>
<main class="graphic">
  <svg class="graphic__backdrop" width="1200" height="1200" viewBox="0 0 1200 1200" aria-hidden="true">
    <defs>
      <radialGradient id="bgGlow" cx="0.85" cy="0.3" r="0.9">
        <stop offset="0" stop-color="#38c8f5"/>
        <stop offset="0.3" stop-color="#0c85d8"/>
        <stop offset="0.7" stop-color="#005aa8"/>
        <stop offset="1" stop-color="#0a4b8e"/>
      </radialGradient>
      <radialGradient id="leftGlow" cx="0" cy="0.3" r="0.5">
        <stop offset="0" stop-color="#1590ef" stop-opacity="0.9"/>
        <stop offset="1" stop-color="#1590ef" stop-opacity="0"/>
      </radialGradient>
      <radialGradient id="halo" cx="0.5" cy="0.3" r="0.7">
        <stop offset="0" stop-color="#a7d6f5"/>
        <stop offset="0.6" stop-color="#5f9fd3"/>
        <stop offset="1" stop-color="#4a87c4"/>
      </radialGradient>
      <linearGradient id="panelFill" x1="0" y1="0" x2="0" y2="1">
        <stop offset="0" stop-color="#2e3a72"/>
        <stop offset="0.15" stop-color="var(--navy)"/>
        <stop offset="1" stop-color="var(--navy)"/>
      </linearGradient>
    </defs>
    <rect class="backdrop__field" width="1200" height="1200" fill="url(#bgGlow)"/>
    <rect class="backdrop__glow" width="1200" height="1200" fill="url(#leftGlow)"/>
    <line class="backdrop__ray" x1="0" y1="0" x2="300" y2="300" stroke="#2a9ff0" stroke-width="3"/>
    <line class="backdrop__ray" x1="1200" y1="0" x2="880" y2="320" stroke="#2a9ff0" stroke-width="3"/>
    <circle class="backdrop__halo" cx="590" cy="597" r="457" fill="url(#halo)"/>
    <circle class="backdrop__ring" cx="590" cy="597" r="362" fill="none" stroke="#1f8fe0" stroke-width="3"/>
    <path class="headline-panel" d="M166 660 H1030 Q1058 660 1066 690 L1200 1197 H0 L130 690 Q138 660 166 660 Z"
          fill="url(#panelFill)" stroke="var(--blue-mist)" stroke-width="2"/>
  </svg>

  <div class="host-photo" role="img" aria-label="Photo of the two course hosts smiling, one in a black turtleneck with arms crossed, one in a blue denim blazer"></div>

  <div class="course-name">The Harvest Ledger Circle</div>

  <h1 class="headline">How to Launch<br>a Multi-Million<br>Business From<br>Scratch</h1>

  <div class="cta">Sign Up Today!</div>
</main>
</body>
</html>
```